physical therapy flyer

2 office locations speciality programs - work injury / Motor vehicle accidents - spanish speaking - do not put balance defecits/ fall prevention - Spanish speaking
neck and back pain shoulder pain/ rotator cuff disorder / bursitis
hip pain knee andle and foot pain post operative care including Spine , shoulder , knee , total joint replacement

Meadowlark Physical therapy & Chiropractic
4871 Pinecrest BLvd
dalton heights ny 10592
7185820147
3715 Tillman Parkway
Fernvale NY 10592
7189043218
www.meadowlarkptrehab.com

```html
<!DOCTYPE html>
<html lang="en">
<head>
<meta charset="utf-8">
<title>Meadowlark Physical Therapy &amp; Chiropractic – Flyer</title>
<link rel="stylesheet" href="https://fonts.googleapis.com/css2?family=Montserrat:wght@400;500;700;800&family=Poppins:wght@400;600;700&family=Oswald:wght@300;500&display=swap">
<style>
  :root {
    --green: #7cbb3c;
    --green-deep: #0f6a34;
    --green-text: #3f9b3f;
    --band-a: #52ad45;
    --band-b: #36985a;
    --charcoal: #2f2f2d;
    --ink: #1c1c1c;
    --white: #ffffff;
  }
  * { box-sizing: border-box; margin: 0; padding: 0; }
  html, body { width: 980px; height: 1200px; overflow: hidden; background: var(--white); }
  .flyer { position: relative; width: 980px; height: 1200px; background: var(--white); font-family: "Poppins", sans-serif; color: var(--ink); overflow: hidden; }

  .hero-photo { position: absolute; left: 300px; top: 0; width: 680px; height: 517px;
    background: linear-gradient(90deg, #ffffff 0%, #eceef0 25%, #d7dadd 45%, #a9b4c0 62%, #6f7f92 78%, #4a4d52 100%); }

  .brand { position: absolute; left: 55px; top: 98px; display: flex; align-items: center; gap: 15px; }
  .brand-dot { width: 58px; height: 58px; border-radius: 50%; background: var(--ink); flex: none; }
  .brand-name { font-family: "Montserrat", sans-serif; font-weight: 500; font-size: 21px; line-height: 1.2; color: var(--ink); }

  .hero-panel { position: absolute; left: 0; top: 193px; width: 522px; height: 354px; background: var(--green);
    border-top-left-radius: 70px; border-top-right-radius: 14px; border-bottom-right-radius: 62px; z-index: 2; padding: 50px 0 0 57px; }
  .hero-title { font-family: "Montserrat", sans-serif; }
  .hero-title .light { display: block; font-weight: 500; font-size: 31px; line-height: 1.25; color: var(--white); white-space: nowrap; }
  .hero-title .bold { display: block; font-weight: 800; font-size: 51px; line-height: 1.0; color: var(--green-deep); letter-spacing: -0.5px; white-space: nowrap; }
  .hero-rule { width: 38px; height: 4px; background: var(--green-deep); margin: 20px 0 10px; }
  .hero-sub { font-family: "Montserrat", sans-serif; font-size: 34px; color: var(--white); line-height: 43px; white-space: nowrap; }
  .hero-sub strong { font-weight: 800; }

  .treatments { position: absolute; left: 0; top: 517px; width: 980px; height: 360px; background: var(--charcoal); }
  .care-photo { position: absolute; left: 0; top: 0; width: 366px; height: 360px;
    background: linear-gradient(100deg, #8a9a88 0%, #3c5fb0 35%, #5fb9b4 65%, #2f2f2d 100%); }
  .treatments-title { position: absolute; left: 397px; top: 42px; font-family: "Poppins", sans-serif; font-weight: 700; font-size: 24px; color: var(--white); white-space: nowrap; }
  .treatments-title span { color: var(--green); }

  .item { position: absolute; display: flex; align-items: center; gap: 22px; height: 44px; }
  .item svg { flex: none; }
  .item-label { font-family: "Poppins", sans-serif; font-weight: 700; font-size: 17px; line-height: 1.3; color: var(--white); white-space: nowrap; }
  .rule-h { position: absolute; height: 0; border-top: 1.5px dashed var(--green); }
  .rule-v { position: absolute; width: 0; border-left: 1.5px dashed var(--green); }

  .check { position: absolute; display: flex; align-items: center; gap: 9px; font-size: 16px; color: var(--white); white-space: nowrap; list-style: none; }

  .language-band { position: absolute; left: 0; top: 877px; width: 980px; height: 48px;
    background: linear-gradient(90deg, var(--band-a), var(--band-b)); color: var(--white);
    font-family: "Montserrat", sans-serif; font-weight: 500; font-size: 22px; letter-spacing: 8.5px;
    display: flex; align-items: center; justify-content: center; white-space: nowrap; }

  .locations-heading { position: absolute; left: 57px; top: 975px; font-family: "Oswald", sans-serif; line-height: 1.05; }
  .locations-heading .thin { display: block; font-weight: 300; font-size: 42px; color: var(--ink); }
  .locations-heading .strong { display: block; font-weight: 500; font-size: 42px; color: var(--green-text); }

  .office { position: absolute; border: 1.5px solid var(--green-text); border-left: none; border-top-right-radius: 14px; border-bottom-right-radius: 14px; }
  .office::after { content: ""; position: absolute; left: -4px; bottom: -4.5px; width: 7px; height: 7px; border-radius: 50%; background: var(--green-text); }
  .office-name { position: absolute; left: -6px; top: -13px; background: var(--white); padding-right: 8px; font-family: "Montserrat", sans-serif; font-weight: 700; font-size: 18px; line-height: 24px; color: var(--green-text); white-space: nowrap; }
  .office-row { position: absolute; left: -6px; display: flex; align-items: flex-start; gap: 17px; }
  .office-row svg { flex: none; margin-top: 2px; }
  .office-address { font-size: 16.5px; line-height: 1.3; color: var(--ink); white-space: nowrap; }
  .office-phone { font-family: "Montserrat", sans-serif; font-weight: 700; font-size: 24px; line-height: 28px; color: var(--ink); letter-spacing: 0.3px; white-space: nowrap; }
  .office-phone-row svg { margin-top: 4px; }
  .office-1 { left: 279px; top: 971px; width: 268px; height: 106px; }
  .office-2 { left: 618px; top: 973px; width: 295px; height: 105px; }

  .website { position: absolute; left: 0; top: 1097px; width: 980px; text-align: center; font-family: "Montserrat", sans-serif; white-space: nowrap; }
  .website .label { font-size: 25px; color: var(--green-text); }
  .website .url { font-weight: 500; font-size: 28px; letter-spacing: 7.5px; color: var(--ink); }
  .website .url b { color: var(--green-text); font-weight: 700; }
</style>
</head>
<body>
<main class="flyer">
  <div class="hero-photo" role="img" aria-label="Therapist examining the shoulder of an older patient seated on a treatment table in a bright clinic"></div>

  <div class="brand">
    <span class="brand-dot"></span>
    <span class="brand-name">Meadowlark Physical Therapy,<br>Chiropractic, and Acupuncture</span>
  </div>

  <section class="hero-panel">
    <h1 class="hero-title">
      <span class="light">MEADOWLARK PHYSICAL</span>
      <span class="bold">THERAPY &amp;</span>
      <span class="bold">CHIROPRACTIC</span>
    </h1>
    <div class="hero-rule"></div>
    <p class="hero-sub">Comprehensive Care<br>Across <strong>Two Locations!</strong></p>
  </section>

  <section class="treatments">
    <div class="care-photo" role="img" aria-label="Physical therapist helping an older man walk between parallel bars"></div>
    <h2 class="treatments-title">SPECIALIZED <span>TREATMENT FOR</span></h2>

    <div class="item" style="left:400px; top:103px;">
      <svg width="40" height="40" viewBox="0 0 40 40"><path d="M10 18a10 10 0 0 1 20 0z" fill="#fff"/><rect x="8" y="18" width="24" height="3" fill="#fff"/><path d="M8 38v-8a6 6 0 0 1 6-6h12a6 6 0 0 1 6 6v8z" fill="#fff"/><circle cx="20" cy="22" r="4" fill="#7cbb3c"/></svg>
      <span class="item-label">Work-Related<br>Injuries</span>
    </div>
    <div class="item" style="left:694px; top:103px;">
      <svg width="42" height="40" viewBox="0 0 40 40"><circle cx="20" cy="8" r="5" fill="#fff"/><rect x="17" y="14" width="6" height="22" rx="2" fill="#fff"/><circle cx="20" cy="20" r="4" fill="#7cbb3c"/><path d="M8 16h24" stroke="#fff" stroke-width="3"/></svg>
      <span class="item-label">Neck, Back, and<br>Shoulder Pain</span>
    </div>

    <div class="rule-v" style="left:663px; top:104px; height:52px;"></div>
    <div class="rule-h" style="left:390px; top:167px; width:260px;"></div>
    <div class="rule-h" style="left:673px; top:167px; width:251px;"></div>

    <div class="item" style="left:387px; top:191px; gap:16px;">
      <svg width="58" height="40" viewBox="0 0 46 40"><rect x="22" y="16" width="22" height="16" rx="3" fill="#7cbb3c"/><circle cx="8" cy="28" r="5" fill="none" stroke="#fff" stroke-width="3"/><path d="M12 26h10" stroke="#fff" stroke-width="3"/><path d="M22 6l2 8 4-5" stroke="#fff" stroke-width="2" fill="none"/></svg>
      <span class="item-label">Motor Vehicle<br>Accident Recovery</span>
    </div>
    <div class="item" style="left:694px; top:191px;">
      <svg width="42" height="40" viewBox="0 0 40 40"><circle cx="16" cy="10" r="5" fill="#fff"/><path d="M10 38l2-18h8l4 10h10v8z" fill="#fff"/><path d="M30 20l4 4" stroke="#7cbb3c" stroke-width="3"/></svg>
      <span class="item-label">Hip, Knee, Ankle,<br>and Foot Pain</span>
    </div>

    <div class="rule-v" style="left:663px; top:180px; height:58px;"></div>
    <div class="rule-h" style="left:390px; top:260px; width:534px;"></div>

    <div class="item" style="left:400px; top:280px;">
      <svg width="40" height="40" viewBox="0 0 40 40"><circle cx="24" cy="8" r="5" fill="#7cbb3c"/><rect x="16" y="14" width="14" height="10" rx="3" fill="#7cbb3c"/><rect x="2" y="26" width="36" height="5" fill="#fff"/><path d="M6 31v7M34 31v7" stroke="#fff" stroke-width="3"/></svg>
      <span class="item-label">Post-Surgical<br>Rehabilitation</span>
    </div>

    <ul>
      <li class="check" style="left:631px; top:284px;"><svg width="14" height="14" viewBox="0 0 14 14"><circle cx="7" cy="7" r="7" fill="#7cbb3c"/><path d="M4 7.2l2 2 4-4" stroke="#fff" stroke-width="1.8" fill="none"/></svg>Spine</li>
      <li class="check" style="left:718px; top:284px;"><svg width="14" height="14" viewBox="0 0 14 14"><circle cx="7" cy="7" r="7" fill="#7cbb3c"/><path d="M4 7.2l2 2 4-4" stroke="#fff" stroke-width="1.8" fill="none"/></svg>Shoulder</li>
      <li class="check" style="left:829px; top:284px;"><svg width="14" height="14" viewBox="0 0 14 14"><circle cx="7" cy="7" r="7" fill="#7cbb3c"/><path d="M4 7.2l2 2 4-4" stroke="#fff" stroke-width="1.8" fill="none"/></svg>Knee</li>
      <li class="check" style="left:631px; top:308px;"><svg width="14" height="14" viewBox="0 0 14 14"><circle cx="7" cy="7" r="7" fill="#7cbb3c"/><path d="M4 7.2l2 2 4-4" stroke="#fff" stroke-width="1.8" fill="none"/></svg>Total Joint Replacements</li>
    </ul>
  </section>

  <div class="language-band">BILINGUAL SERVICES – SPANISH AVAILABLE</div>

  <h2 class="locations-heading"><span class="thin">OUR TWO</span><span class="strong">LOCATIONS</span></h2>

  <div class="office office-1">
    <span class="office-name">DALTON HEIGHTS</span>
    <div class="office-row" style="top:22px;">
      <svg width="20" height="20" viewBox="0 0 20 20"><path d="M10 1a7 7 0 0 1 7 7c0 5-7 11-7 11S3 13 3 8a7 7 0 0 1 7-7z" fill="#3f9b3f"/><circle cx="10" cy="8" r="2.6" fill="#fff"/></svg>
      <span class="office-address">4871 Pinecrest Blvd,<br>NY 10592</span>
    </div>
    <div class="office-row office-phone-row" style="top:70px;">
      <svg width="20" height="20" viewBox="0 0 20 20"><circle cx="10" cy="10" r="9" fill="#3f9b3f"/><path d="M7 5.5l2 2-1 1.5a6 6 0 0 0 3 3l1.5-1 2 2-1.5 1.5c-3 0-7-4-7-7z" fill="#fff"/></svg>
      <span class="office-phone">718-582-0147</span>
    </div>
  </div>

  <div class="office office-2">
    <span class="office-name">FERNVALE</span>
    <div class="office-row" style="top:22px;">
      <svg width="20" height="20" viewBox="0 0 20 20"><path d="M10 1a7 7 0 0 1 7 7c0 5-7 11-7 11S3 13 3 8a7 7 0 0 1 7-7z" fill="#3f9b3f"/><circle cx="10" cy="8" r="2.6" fill="#fff"/></svg>
      <span class="office-address">3715 Tillman Parkway,<br>NY 10592</span>
    </div>
    <div class="office-row office-phone-row" style="top:70px;">
      <svg width="20" height="20" viewBox="0 0 20 20"><circle cx="10" cy="10" r="9" fill="#3f9b3f"/><path d="M7 5.5l2 2-1 1.5a6 6 0 0 0 3 3l1.5-1 2 2-1.5 1.5c-3 0-7-4-7-7z" fill="#fff"/></svg>
      <span class="office-phone">718-904-3218</span>
    </div>
  </div>

  <p class="website"><span class="label">Visit our website: </span><span class="url">www.<b>meadowlarkptrehab</b>.com</span></p>
</main>
</body>
</html>
```